Business Card for brovaLINK

Create a Business Card with an existing logo for brovaLINK AG. We are a Information Technology company that does consulting and developing SW to automate business processes. The main colors are given from the logo.

Industry/Entity Type

Business

Requirements
Nice to have
• we use a a font style Century Gothic in our documents

```html
<!DOCTYPE html>
<html lang="en">
<head>
<meta charset="utf-8">
<title>brovaLINK – Business Card</title>
<link rel="stylesheet" href="https://fonts.googleapis.com/css2?family=Questrial&display=swap">
<style>
  :root {
    --stage: #e7e8ea;
    --paper: #f7f7f7;
    --ink: #4a4a4a;
    --ink-soft: #6d6d6d;
    --rule: #9a9a9a;
    --rule-dark: #3a3a3a;
    --brand-blue: #2a7fc7;
    --brand-blue-light: #8cc4ee;
    --brand-green: #5aa832;
  }
  * { box-sizing: border-box; margin: 0; padding: 0; }
  html, body { width: 1200px; height: 900px; overflow: hidden; }
  body {
    background: var(--stage);
    font-family: "Questrial", "Century Gothic", sans-serif;
    color: var(--ink);
    position: relative;
  }
  .card {
    position: absolute;
    left: 320px;
    width: 560px;
    height: 340px;
    background: var(--paper);
    box-shadow: 0 6px 18px rgba(0,0,0,0.12);
    overflow: hidden;
  }
  .card--front { top: 70px; }
  .card--back  { top: 480px; }

  .wordmark {
    position: absolute;
    font-size: 40px;
    line-height: 1;
    color: var(--ink);
    letter-spacing: 0.5px;
    display: flex;
    align-items: center;
    gap: 12px;
    white-space: nowrap;
  }
  .wordmark__dot {
    width: 24px; height: 24px;
    border-radius: 50%;
    background: var(--brand-blue);
  }
  .card--front .wordmark { left: 44px; top: 40px; }
  .card--back .wordmark { right: 40px; top: 170px; }

  .front-accent {
    position: absolute;
    right: 0; bottom: 0;
    width: 210px; height: 190px;
    background: linear-gradient(150deg, #e9ecef 0%, var(--brand-blue-light) 45%, var(--brand-blue) 100%);
  }

  .identity { position: absolute; left: 34px; top: 28px; }
  .identity__name {
    font-size: 11px; line-height: 15px; letter-spacing: 3px; text-transform: uppercase; color: var(--ink-soft);
  }
  .identity__role { font-size: 11px; line-height: 15px; letter-spacing: 1.5px; color: var(--brand-green); }
  .identity__company { font-size: 11px; line-height: 15px; font-weight: bold; color: var(--brand-blue); margin-top: 12px; letter-spacing: 0.8px; }
  .identity__address { font-size: 11px; line-height: 16px; color: var(--ink-soft); letter-spacing: 0.8px; }

  .divider { position: absolute; left: 34px; top: 150px; right: 34px; height: 1px; background: var(--rule); }
  .divider__accent { position: absolute; left: 0; top: -1px; width: 120px; height: 3px; background: var(--rule-dark); }

  .contact {
    position: absolute; right: 34px; bottom: 20px;
    list-style: none; text-align: right;
    font-size: 12px; letter-spacing: 1.6px; color: var(--ink);
  }
  .contact li { display: flex; justify-content: flex-end; align-items: center; gap: 12px; line-height: 20px; }
  .contact svg { width: 12px; height: 12px; fill: var(--brand-blue); }
</style>
</head>
<body>
  <section class="card card--front" aria-label="Card front">
    <div class="wordmark"><span class="wordmark__dot"></span>brovaLINK</div>
    <div class="front-accent" role="img" aria-label="Large brand decoration in blue, green and grey tones"></div>
  </section>

  <section class="card card--back" aria-label="Card back">
    <div class="identity">
      <p class="identity__name">Lukas Brenner</p>
      <p class="identity__role">CEO</p>
      <p class="identity__company">brovaLINK</p>
      <p class="identity__address">Lindenweg 12<br>5400 Baden<br>Switzerland</p>
    </div>
    <div class="divider"><span class="divider__accent"></span></div>

    <div class="wordmark"><span class="wordmark__dot"></span>brovaLINK</div>

    <ul class="contact">
      <li>+41 56 000 12 34
        <svg viewBox="0 0 24 24" aria-hidden="true"><path d="M6.6 10.8a15 15 0 0 0 6.6 6.6l2.2-2.2c.3-.3.7-.4 1-.2 1.1.4 2.3.6 3.6.6.6 0 1 .4 1 1V20c0 .6-.4 1-1 1A17 17 0 0 1 3 4c0-.6.4-1 1-1h3.5c.6 0 1 .4 1 1 0 1.3.2 2.5.6 3.6.1.3 0 .7-.2 1z"/></svg></li>
      <li>+41 79 000 56 78
        <svg viewBox="0 0 24 24" aria-hidden="true"><path d="M7 1h10a2 2 0 0 1 2 2v18a2 2 0 0 1-2 2H7a2 2 0 0 1-2-2V3a2 2 0 0 1 2-2zm0 3v15h10V4z"/></svg></li>
      <li>lukas.brenner@brovalink.ch
        <svg viewBox="0 0 24 24" aria-hidden="true"><path d="M2 5h20v14H2zm2 2v.5l8 5 8-5V7l-8 5z"/></svg></li>
      <li>www.brovalink.ch
        <svg viewBox="0 0 24 24" aria-hidden="true"><path d="M12 2a10 10 0 1 0 0 20 10 10 0 0 0 0-20zm0 2c1 1.3 1.8 3 2.1 5H9.9C10.2 7 11 5.3 12 4zM4.3 11h3.6c0 .7 0 1.3.1 2H4.3a8 8 0 0 1 0-2zm5.6 0h4.2v2H9.9zm6.2 0h3.6a8 8 0 0 1 0 2h-3.6zM9.9 15h4.2c-.3 2-1.1 3.7-2.1 5-1-1.3-1.8-3-2.1-5z"/></svg></li>
    </ul>
  </section>
</body>
</html>
```